Harborline Renewal Business Card Design

Professional and clean design. The design colors should flow with the logo. Two-sided card with the website on the back which is:

www.HarborlineRenewal.example.

"Specializing in Water Damage Restoration"

On the front I need the name, email, phone, and logo.

Name: Darnell Quisby
Email: Darnell@HarborlineRenewal.example
Phone: 555-318-2046 for now

I only have the Preview and Thumbnail right now but should have the source files uploaded within a day or two.

Target Market(s)

Flood victims, home owners with water damage from busted pipes etc...

Industry/Entity Type

Business

Contact Information for Business Card

Name: Darnell Quisby

Font styles to use
Serif
Sans Serif

Requirements
Must have
• Business Card Details Info

```html
<!DOCTYPE html>
<html lang="en">
<head>
<meta charset="utf-8">
<title>Harborline Renewal Business Card</title>
<link rel="stylesheet" href="https://fonts.googleapis.com/css2?family=Cinzel:wght@500&family=Open+Sans:wght@400;600&display=swap">
<style>
  :root {
    --sky: #55c1ef;
    --brand: #3b9fd6;
    --brand-deep: #2f8ac4;
    --paper: #ffffff;
    --ink: #222222;
    --canvas: #eef0f2;
  }
  * { box-sizing: border-box; margin: 0; padding: 0; }
  html, body {
    width: 1200px; height: 900px; overflow: hidden;
    background: var(--canvas);
    font-family: "Open Sans", Arial, sans-serif;
  }
  .stage { position: relative; width: 1200px; height: 900px; }
  .card {
    position: absolute; width: 640px; height: 366px;
    box-shadow: 0 6px 18px rgba(0,0,0,0.18);
  }
  .card-back {
    left: 110px; top: 80px; background: var(--sky);
    display: flex; flex-direction: column; align-items: center; justify-content: center;
  }
  .card-front { left: 450px; top: 460px; background: var(--paper); }
  .brand { display: flex; align-items: center; gap: 16px; }
  .brand-dot { width: 62px; height: 62px; border-radius: 50%; flex: none; }
  .brand-name {
    font-family: "Cinzel", Georgia, serif; font-weight: 500;
    font-size: 34px; letter-spacing: 2px; white-space: nowrap;
  }
  .card-back .brand-dot { background: var(--brand-deep); }
  .card-back .brand-name { color: var(--brand-deep); }
  .back-url { margin-top: 22px; color: var(--paper); font-weight: 600; font-size: 15px; }
  .back-tagline { margin-top: 14px; color: var(--paper); font-weight: 600; font-size: 19px; }
  .contact { position: absolute; left: 330px; top: 46px; }
  .contact-name { color: var(--brand); font-weight: 600; font-size: 20px; margin-bottom: 14px; }
  .contact-line {
    display: flex; align-items: center; gap: 8px;
    color: var(--ink); font-size: 13.5px; margin-bottom: 6px;
  }
  .contact-line svg { width: 12px; height: 12px; flex: none; fill: var(--brand); }
  .card-front .brand { position: absolute; left: 60px; bottom: 62px; }
  .card-front .brand-dot { background: var(--brand); }
  .card-front .brand-name { color: var(--brand); }
</style>
</head>
<body>
<main class="stage">
  <section class="card card-back" aria-label="Card back">
    <div class="brand">
      <span class="brand-dot"></span>
      <span class="brand-name">Harborline Renewal</span>
    </div>
    <p class="back-url">www.HarborlineRenewal.example</p>
    <p class="back-tagline">Specializing in Water Damage Restoration</p>
  </section>

  <section class="card card-front" aria-label="Card front">
    <div class="contact">
      <p class="contact-name">Darnell Quisby</p>
      <p class="contact-line">
        <svg viewBox="0 0 24 24" aria-hidden="true"><path d="M6.6 10.8c1.4 2.8 3.8 5.1 6.6 6.6l2.2-2.2c.3-.3.7-.4 1-.2 1.1.4 2.3.6 3.6.6.6 0 1 .4 1 1V20c0 .6-.4 1-1 1C10.6 21 3 13.4 3 4c0-.6.4-1 1-1h3.5c.6 0 1 .4 1 1 0 1.3.2 2.5.6 3.6.1.3 0 .7-.2 1z"/></svg>
        555-318-2046
      </p>
      <p class="contact-line">
        <svg viewBox="0 0 24 24" aria-hidden="true"><path d="M2 5h20v14H2z M4 7v.5l8 5 8-5V7l-8 5z" fill-rule="evenodd"/></svg>
        Darnell@HarborlineRenewal.example
      </p>
    </div>
    <div class="brand">
      <span class="brand-dot"></span>
      <span class="brand-name">Harborline Renewal</span>
    </div>
  </section>
</main>
</body>
</html>
```